MRT Property - Business Cards

Looking for a business card & general letterhead, signage etc design for our new logo.

Colours:
000a20
0056a2
00b5ef
0088ce
68cef2

Fonts:
Poppins
Karla

Please keep look and feel of new brand - example in the zip package I sent.

```html
<!DOCTYPE html>
<html lang="en">
<head>
<meta charset="utf-8">
<title>MRT Property – Business Card</title>
<link href="https://fonts.googleapis.com/css2?family=Montserrat:wght@400;500;700;800&family=Shadows+Into+Light&display=swap" rel="stylesheet">
<style>
  :root {
    --ink: #000a20;
    --brand-deep: #0056a2;
    --brand-royal: #0b54a4;
    --brand-cyan: #00b5ef;
    --brand-mid: #0088ce;
    --brand-sky: #68cef2;
    --paper: #ffffff;
    --stage: #e9ecf1;
  }
  * { box-sizing: border-box; margin: 0; padding: 0; }
  html, body { width: 1200px; height: 931px; overflow: hidden; }
  body {
    background: var(--stage);
    font-family: "Montserrat", sans-serif;
    display: flex;
    flex-direction: column;
    align-items: center;
    justify-content: center;
    gap: 40px;
  }
  .card {
    width: 700px;
    height: 400px;
    border-radius: 22px;
    position: relative;
    overflow: hidden;
    box-shadow: 0 6px 18px rgba(0, 10, 32, 0.18);
  }
  .card-front {
    background: var(--brand-royal);
    display: flex;
    align-items: center;
    justify-content: center;
  }
  .wordmark {
    display: flex;
    align-items: center;
    gap: 18px;
    font-weight: 800;
    letter-spacing: 1px;
  }
  .wordmark-dot {
    width: 40px;
    height: 40px;
    border-radius: 50%;
  }
  .card-front .wordmark { color: var(--paper); font-size: 64px; }
  .card-front .wordmark-dot { background: var(--brand-sky); }

  .card-back { background: var(--paper); }
  .card-back .wordmark {
    position: absolute;
    top: 42px;
    right: 60px;
    color: var(--brand-royal);
    font-size: 48px;
  }
  .card-back .wordmark-dot { width: 32px; height: 32px; background: var(--brand-mid); }
  .rule {
    position: absolute;
    height: 2px;
    background: var(--brand-royal);
  }
  .rule-top { top: 138px; left: 250px; right: 40px; }
  .rule-name { top: 248px; left: 44px; width: 250px; }
  .person {
    position: absolute;
    left: 44px;
    top: 168px;
    color: var(--ink);
  }
  .person-name {
    font-family: "Shadows Into Light", cursive;
    font-size: 46px;
    line-height: 1;
  }
  .person-role { font-size: 15px; font-weight: 500; margin-top: 4px; }
  .contacts {
    position: absolute;
    left: 44px;
    top: 266px;
    list-style: none;
    font-size: 16px;
    color: var(--ink);
  }
  .contacts li { display: flex; align-items: center; gap: 12px; height: 26px; }
  .contacts svg { width: 18px; height: 18px; fill: var(--brand-royal); }
  .address {
    position: absolute;
    right: 40px;
    top: 190px;
    font-size: 15px;
    line-height: 1.35;
    color: var(--ink);
    text-align: left;
  }
  .band {
    position: absolute;
    left: 0; right: 0; bottom: 0;
    height: 16px;
    display: flex;
  }
  .band span { flex: 1; }
  .band .b1 { background: var(--brand-sky); }
  .band .b2 { background: var(--brand-cyan); }
  .band .b3 { background: var(--brand-mid); }
  .band .b4 { background: var(--brand-deep); }
</style>
</head>
<body>
  <section class="card card-front">
    <div class="wordmark"><span class="wordmark-dot"></span>MRT Property</div>
  </section>

  <section class="card card-back">
    <div class="wordmark"><span class="wordmark-dot"></span>MRT Property</div>
    <div class="rule rule-top"></div>

    <div class="person">
      <p class="person-name">Daniel Hart</p>
      <p class="person-role">Managing Director</p>
    </div>
    <div class="rule rule-name"></div>

    <ul class="contacts">
      <li>
        <svg viewBox="0 0 24 24" aria-hidden="true"><path d="M6.6 10.8a15 15 0 0 0 6.6 6.6l2.2-2.2a1 1 0 0 1 1-.25 11.4 11.4 0 0 0 3.6.6 1 1 0 0 1 1 1V20a1 1 0 0 1-1 1A17 17 0 0 1 3 4a1 1 0 0 1 1-1h3.5a1 1 0 0 1 1 1c0 1.25.2 2.45.6 3.6a1 1 0 0 1-.25 1z"/></svg>
        1 (555) 014-2290
      </li>
      <li>
        <svg viewBox="0 0 24 24" aria-hidden="true"><path d="M2 5h20v14H2z M2 5l10 8 10-8" /></svg>
        info@mrtproperty.com
      </li>
      <li>
        <svg viewBox="0 0 24 24" aria-hidden="true"><path d="M12 2a10 10 0 1 0 0 20 10 10 0 0 0 0-20zm0 2c.9 1.2 1.6 2.9 1.9 5h-3.8c.3-2.1 1-3.8 1.9-5zM4.3 14a8 8 0 0 1 0-4h3.8a16 16 0 0 0 0 4zm5.8 0a14 14 0 0 1 0-4h3.8a14 14 0 0 1 0 4zm5.8 0a16 16 0 0 0 0-4h3.8a8 8 0 0 1 0 4zM12 20c-.9-1.2-1.6-2.9-1.9-5h3.8c-.3 2.1-1 3.8-1.9 5z"/></svg>
        www.mrtproperty.com
      </li>
    </ul>

    <p class="address">420 Maple Crest Ave Suite<br>210 Dayton Ohio 45402</p>

    <div class="band"><span class="b1"></span><span class="b2"></span><span class="b3"></span><span class="b4"></span></div>
  </section>
</body>
</html>
```